Emerging automotive detailing business

I am starting a small automotive detailing business in hopes of becoming a well-known detailer to work on high end cars. I would like a card to reflect the high quality and time I put into my work. The name of the company is Bright Crest Detailing. I feel like it represents racecars getting off the line at the drag strip as well as an innuendo of "Up the Ladder". I do minor paint correction such as clay barring, multi-step buffing and polishing, waxing, hand washes, etc. I am always striving to learn more and improve my work. My goal is to have total customer satisfaction. This is a female run business but I do not want it to be very girly. Elegant is okay! I have pictures of my personal wrenfield attached, they do not need to be incorporated but if you can think of a cool way to use 1 or all of them, go for it!

Target Market(s)

Anyone that owns a vehicle. Preferably high end vehicles such as Valtori, Castellverde and Morvani but I will also happily work on any car, truck or suv no matter what brand.

Industry/Entity Type

Automotive

Contact Information for Business Card

Bright Crest Detailing
Mira Tolland
4175 Quenhollow Rd
Ashmere PA 17492
Cell phone- call/text- 717-555-0148
email- brightcrestdetails@maildrop-example.com
Instagram: @brightcrestdetailing
Facebook: facebook.com/brightcrestdetailing

Requirements
Must have
• Business name, my name, address, phone number. Listing that I do minor paint correction such as clay barring, multi-step buffing and polishing, waxing, hand washes, interior cleaning, and more. (This last part was in nice to haves but I have realized that I do really want it, so I moved it to must haves.) I want something that is different and eye-catching to my customers. Some people have done this very well with cards already submitted to me, but a lot have not. I didn't mess with the "look and feel bars" much because because I am pretty open to the overall design as long as it is not your basic run of the mill design.
Nice to have
• Something car related. Maybe an appointment time/date line. I do not have a logo, but if you would like to design one and incorporate it, that would be amazing!
Should not have
• Purple and Pink colors. Boring, basic, normal card.

```html
<!DOCTYPE html>
<html lang="en">
<head>
<meta charset="utf-8">
<title>Bright Crest Detailing – Business Card</title>
<link href="https://fonts.googleapis.com/css2?family=Varela+Round&family=Nunito:wght@800&family=Lato:wght@300;400;700&display=swap" rel="stylesheet">
<style>
  :root {
    --page-bg: #e9e7e3;
    --card-black: #050505;
    --card-edge: #1a1a1a;
    --text-white: #ffffff;
    --text-soft: #cfcfcf;
    --band-white: #f7f7f7;
    --band-text: #1c1c1c;
    --photo-dark: #151a17;
    --photo-mid: #36413a;
    --photo-light: #6b7a72;
  }
  * { margin: 0; padding: 0; box-sizing: border-box; }
  html, body {
    width: 1200px;
    height: 1023px;
    overflow: hidden;
    background: var(--page-bg);
  }
  .canvas {
    position: relative;
    width: 1200px;
    height: 1023px;
    display: flex;
    flex-direction: column;
    align-items: center;
    justify-content: center;
    gap: 70px;
  }
  .card {
    position: relative;
    width: 560px;
    height: 320px;
    border-radius: 4px;
    overflow: hidden;
    box-shadow: 0 10px 30px rgba(0,0,0,0.25);
  }

  /* Front */
  .card-front {
    background: linear-gradient(160deg, #141414 0%, var(--card-black) 45%, #000 100%);
    color: var(--text-white);
    padding: 44px 40px 0 70px;
  }
  .business-name {
    font-family: "Nunito", "Varela Round", sans-serif;
    font-weight: 800;
    font-size: 33px;
    letter-spacing: 0.3px;
    line-height: 1;
  }
  .address {
    font-family: "Lato", sans-serif;
    font-weight: 300;
    font-size: 17px;
    color: var(--text-soft);
    margin-top: 8px;
    margin-left: 36px;
  }
  .owner-name {
    font-family: "Nunito", "Varela Round", sans-serif;
    font-weight: 800;
    font-size: 27px;
    margin-top: 26px;
    margin-left: 150px;
  }
  .contact-list {
    list-style: none;
    font-family: "Lato", sans-serif;
    font-size: 16px;
    line-height: 1.55;
    margin-top: 26px;
    margin-left: 118px;
  }
  .contact-list .label { font-weight: 400; color: var(--text-white); }
  .contact-list .value { font-weight: 300; color: var(--text-soft); }

  /* Back */
  .card-back {
    background: var(--band-white);
  }
  .vehicle-photo {
    position: absolute;
    left: 0; top: 0;
    width: 560px;
    height: 236px;
    background: radial-gradient(ellipse at 65% 55%, var(--photo-light) 0%, var(--photo-mid) 35%, var(--photo-dark) 80%);
  }
  .service-list {
    position: absolute;
    left: 0; right: 0;
    top: 200px;
    display: flex;
    justify-content: center;
    gap: 14px;
    list-style: none;
    font-family: "Lato", sans-serif;
    font-size: 15px;
    color: var(--text-white);
  }
  .service-list li::before { content: "• "; }
  .service-list li.more::before { content: ""; }
  .appointment-band {
    position: absolute;
    left: 0; right: 0; bottom: 0;
    height: 84px;
    display: flex;
    align-items: center;
    justify-content: center;
    font-family: "Lato", sans-serif;
    font-size: 18px;
    color: var(--band-text);
  }
  .appointment-line {
    display: inline-block;
    width: 240px;
    border-bottom: 1px solid var(--band-text);
    margin-left: 10px;
    transform: translateY(6px);
  }
</style>
</head>
<body>
<main class="canvas">
  <section class="card card-front" aria-label="Business card front">
    <h1 class="business-name">Bright Crest Detailing</h1>
    <p class="address">4175 Quenhollow Rd. Ashmere PA 17492</p>
    <h2 class="owner-name">Mira Tolland</h2>
    <ul class="contact-list">
      <li><span class="label">Cell/Text:</span> <span class="value">717-555-0148</span></li>
      <li><span class="label">Instagram:</span> <span class="value">@brightcrestdetailing</span></li>
      <li><span class="label">Facebook:</span> <span class="value">brightcrestdetailing</span></li>
      <li><span class="label">Email-</span> <span class="value">brightcrestdetails@maildrop-example.com</span></li>
    </ul>
  </section>

  <section class="card card-back" aria-label="Business card back">
    <div class="vehicle-photo" role="img" aria-label="Photo of a detailed car on a dark road"></div>
    <ul class="service-list">
      <li>Clay barring</li>
      <li>Buffing &amp; polishing</li>
      <li>Waxing</li>
      <li>Hand washes</li>
      <li class="more">and more</li>
    </ul>
    <div class="appointment-band">Appointment:<span class="appointment-line"></span></div>
  </section>
</main>
</body>
</html>
```